Book cover - Lanterns Along the Winding Quay

Book cover for Ebook (Quillet) and wrap around print cover (Bindwell) (back, front, and spine)

The book title (may slightly change by end of brief):
(MAIN TITLE) 'Lanterns Along the Winding Quay'
(SUB HEADING) 'A Practical Seasonal Garden Companion for Planting Bulbs, Pruning Hedges and Growing Fresh Herbs'
by Dr Owen Pratchard

I would like a bold, stand out cover. Contemporary. I would like to avoid stereotypical images of people looking anxious or worried. I would like the design to be more uplifting and hopeful, rather than focusing on the negative aspect of anxiety, but avoiding cliched photos of people raising their hands in the air, smiling and jumping etc. The cover should appeal to both men and women.

Trim size of book cover (for BindWell) is 5.25" x 8" back and front with a spine size of 0.477 inches
Updates

Reason: I have decided to extend the deadline by 1 more day, not because I am unhappy with the quality of the designs, but because a few designers have contacted me to explain they have had technical difficulties when submitting their files. Thanks everyone for the hard work and great designs.

Target Market(s)

Males and females (16+) who struggle with social anxiety and shyness

Industry/Entity Type

Social

Font styles to use
Serif

Requirements
Must have
• Bold cover that is modern and contemporary. For example, I like these covers:
• http://lnkvo.test/7kTq3Wm
• http://lnkvo.test/9gHw5Ze
• http://lnkvo.test/4nVy8Kb
• http://lnkvo.test/6jFu2Xo
• http://lnkvo.test/3mEs9Lt
• http://lnkvo.test/8hGz4Nd
• http://lnkvo.test/5bJk7Pv
Nice to have
• Open to abstract designs.
Should not have
• No stereotypical pictures of people who look anxious or worried. Avoid cliched photos of people raising their hands in the air, smiling and jumping etc.

```html
<!DOCTYPE html>
<html lang="en">
<head>
<meta charset="UTF-8">
<title>Lanterns Along the Winding Quay — Book Cover</title>
<link rel="stylesheet" href="https://fonts.googleapis.com/css2?family=Poppins:wght@500;600&family=Roboto:wght@400;500&display=swap">
<style>
  :root {
    --page-bg: #ffffff;
    --cover-bg: #050505;
    --text-light: #ffffff;
    --accent-blue: #7ec8f0;
    --powder-pink: #e8367a;
    --powder-yellow: #f4d21c;
    --powder-green: #3fbf4a;
    --powder-cyan: #2ec3e0;
    --powder-purple: #6a3ac8;
    --powder-red: #d8262e;
    --powder-orange: #f28a1c;
  }
  html, body {
    margin: 0;
    padding: 0;
    width: 1200px;
    height: 1200px;
    overflow: hidden;
    background: var(--page-bg);
  }
  .canvas {
    position: relative;
    width: 1200px;
    height: 1200px;
  }
  .book-cover {
    position: absolute;
    left: 239px;
    top: 50px;
    width: 722px;
    height: 1100px;
    background: var(--cover-bg);
    overflow: hidden;
  }
  .subtitle {
    position: absolute;
    top: 86px;
    left: 0;
    right: 0;
    margin: 0;
    text-align: center;
    font-family: "Roboto", Arial, sans-serif;
    line-height: 1.28;
  }
  .subtitle-lead {
    display: block;
    color: var(--accent-blue);
    font-weight: 500;
    font-size: 20px;
  }
  .subtitle-rest {
    display: block;
    color: var(--text-light);
    font-weight: 400;
    font-size: 18px;
    letter-spacing: 1.5px;
    width: 380px;
    margin: 0 auto;
  }
  .color-burst {
    position: absolute;
    left: 10px;
    top: 210px;
    width: 700px;
    height: 660px;
    background: conic-gradient(from 200deg at 50% 52%,
      var(--powder-purple), var(--powder-green), var(--powder-cyan),
      var(--powder-red), var(--powder-yellow), var(--powder-orange),
      var(--powder-pink), var(--powder-purple));
    -webkit-mask-image: radial-gradient(closest-side, #000 35%, rgba(0,0,0,0.55) 70%, transparent 100%);
    mask-image: radial-gradient(closest-side, #000 35%, rgba(0,0,0,0.55) 70%, transparent 100%);
    filter: saturate(1.1);
  }
  .title {
    position: absolute;
    left: 0;
    right: 0;
    top: 440px;
    margin: 0;
    text-align: center;
    font-family: "Poppins", "Century Gothic", sans-serif;
    font-weight: 600;
    color: var(--text-light);
    text-shadow: 2px 3px 4px rgba(0,0,0,0.55);
    line-height: 1;
  }
  .title-main {
    display: block;
    font-size: 70px;
    letter-spacing: 3px;
  }
  .title-second {
    display: block;
    font-size: 38px;
    margin-top: 14px;
  }
  .title-third {
    display: block;
    font-size: 46px;
    margin-top: 14px;
  }
  .author {
    position: absolute;
    left: 0;
    right: 0;
    top: 995px;
    margin: 0;
    text-align: center;
    font-family: "Roboto", Arial, sans-serif;
    font-weight: 400;
    font-size: 38px;
    color: var(--text-light);
    letter-spacing: 1px;
  }
</style>
</head>
<body>
  <div class="canvas">
    <section class="book-cover">
      <p class="subtitle">
        <span class="subtitle-lead">A Practical Seasonal Garden Companion</span>
        <span class="subtitle-rest">for Planting Bulbs, Pruning Hedges and Growing Fresh Herbs</span>
      </p>
      <div class="color-burst" role="img" aria-label="Explosion of coloured powder in green, cyan, red, yellow, pink and purple on black"></div>
      <h1 class="title">
        <span class="title-main">LANTERNS</span>
        <span class="title-second">ALONG THE WINDING</span>
        <span class="title-third">QUAY</span>
      </h1>
      <p class="author">by Dr Owen Pratchard</p>
    </section>
  </div>
</body>
</html>
```